Business Card for a Life Coaching Company

MOSSVALE is a Life Coaching company that was initiated to support people who want to transform thier life or ana aspect of it.
our slogan is : "Dream. Believe. Succeed"
our logo is uploaded.
The name of the company implies that leadership, strength and wisdom required to change your life.
We want an attractive business card that would give an impression of reliability, support and change. so we really want it unique. Here are some examples of unique cards:

http://www.pixelharbornotes.example/2009/05/100-really-creative-business-cards/

MossVale is a life coaching organization focusing on individual transformation through the application of relevant and timeless principles of success.  MossVale believes that real, sustainable life transformations are brought about by tuning into the timeless wisdom we each carry in our hearts while boldy acting in the direction of our dreams.

Contacts on the card:
Address: 7 Tarek Ibn Nabil Heliopolis Cairo Egypt
Tel: +202 24 81 37 52
Fax: +202 24 81 37 19
Mobile: +2 012 574 9026 (Nadia Sherif)
+2 0199915815 (Kamal Rashidi)

By the way, our temporary website is http://www.mossvale.example

We have attached an .eps file with various configurations of our logo.

```html
<!DOCTYPE html>
<html lang="en">
<head>
<meta charset="utf-8">
<title>MOSSVALE Business Card</title>
<link rel="stylesheet" href="https://fonts.googleapis.com/css2?family=Marcellus&family=Didact+Gothic&display=swap">
<style>
  :root {
    --card-bg: #ffffff;
    --brand-orange: #ff6a00;
    --soft-orange: #ffb27a;
    --text-grey: #7d7d7d;
    --wordmark-grey: #8a8a8a;
  }
  html, body {
    margin: 0;
    padding: 0;
    width: 1200px;
    height: 686px;
    overflow: hidden;
    background: var(--card-bg);
  }
  .card {
    position: relative;
    width: 1200px;
    height: 686px;
    background: var(--card-bg);
    overflow: hidden;
  }
  .top-wave {
    position: absolute;
    top: 0;
    left: 0;
    width: 1200px;
    height: 686px;
  }
  .lion-artwork {
    position: absolute;
    left: 0;
    top: 30px;
    width: 360px;
    height: 656px;
    background: linear-gradient(100deg, var(--brand-orange) 0%, var(--soft-orange) 55%, rgba(255,255,255,0) 100%);
    border-top-right-radius: 60% 30%;
    opacity: 0.9;
  }
  .details {
    position: absolute;
    left: 778px;
    top: 0;
    transform: translateX(-50%);
    text-align: center;
    white-space: nowrap;
  }
  .wordmark {
    margin: 186px 0 0;
    font-family: "Marcellus", serif;
    font-weight: 400;
    font-size: 100px;
    line-height: 1;
    letter-spacing: 0.14em;
    margin-right: -0.14em;
    color: var(--wordmark-grey);
  }
  .person-name {
    margin: 34px 0 0;
    font-family: "Didact Gothic", sans-serif;
    font-size: 44px;
    line-height: 1;
    letter-spacing: 0.08em;
    color: var(--brand-orange);
  }
  .address {
    margin: 26px 0 0;
    font-family: "Didact Gothic", sans-serif;
    font-size: 23px;
    letter-spacing: 0.1em;
    color: var(--text-grey);
  }
  .contact-list {
    list-style: none;
    margin: 50px 0 0;
    padding: 0;
    font-family: "Didact Gothic", sans-serif;
    font-size: 29px;
    line-height: 47px;
    letter-spacing: 0.08em;
  }
  .contact-label { color: var(--text-grey); }
  .contact-value { color: var(--brand-orange); }
</style>
</head>
<body>
  <main class="card">
    <svg class="top-wave" viewBox="0 0 1200 686" aria-hidden="true">
      <path fill="var(--brand-orange)" d="M220 0 C 380 70, 620 60, 880 45 C 1050 35, 1150 90, 1200 185 L1200 0 Z"/>
    </svg>
    <div class="lion-artwork" role="img" aria-label="Orange lion head illustration"></div>
    <section class="details">
      <h1 class="wordmark">MOSSVALE</h1>
      <p class="person-name">Nadia Sherif</p>
      <p class="address">7 Tarek Ibn Nabil Heliopolis Cairo Egypt.</p>
      <ul class="contact-list">
        <li><span class="contact-label">Tel:</span> <span class="contact-value">+202 24 81 37 52</span></li>
        <li><span class="contact-label">Fax:</span> <span class="contact-value">+202 24 81 37 19</span></li>
        <li><span class="contact-label">Mobile:</span> <span class="contact-value">+2 012 574 9026</span></li>
      </ul>
    </section>
  </main>
</body>
</html>
```